Brochure and Business Card design

I am looking for a high end, elegant A4, 4 page brochure booklet to convey our products to clientele that will be visiting a luxury display showroom.

Harrowgate Locks and Grilles is a Australian security provider, and we supply high end products from reputable brands.
The brochure will be directed to clients building a new home with a partnered building company and will be accompanied with display boards of our products.

I am providing files of a document we have put together with the relevant information and some images to help along the way, we are not bound by the layout or style it has been drawn up and we wish to give you complete creative freedom putting the peaces together. I have also provided the files for our logo in two different colours, and a picture of a brochure we love the look of.

If you have any suggestions, we can likely come up with further images etc if it will help or even if you feel some should be removed, we are open to that also

Target Market(s)

Young familys, people building new luxury homes, proffesionals, home owners

Industry/Entity Type

Business

Font styles to use
Serif
Sans Serif

Requirements
Must have
• All 8 pages
Should not have
• Not really a fan of reds and similar.

```html
<!DOCTYPE html>
<html lang="en">
<head>
<meta charset="utf-8">
<title>Ducted Vacuum – Brochure Spread</title>
<link rel="stylesheet" href="https://fonts.googleapis.com/css2?family=Questrial&family=Open+Sans:wght@600;700&display=swap">
<style>
  :root {
    --backdrop: #cfcfcf;
    --paper: #ffffff;
    --blue-top: #1f76c4;
    --blue-bottom: #2aa3e0;
    --green: #8cc63f;
    --ink: #5b5b5b;
    --label: #1a1a1a;
    --placeholder-grey: #e4e6e9;
  }
  * { margin: 0; padding: 0; box-sizing: border-box; }
  html, body { width: 1200px; height: 645px; overflow: hidden; background: var(--backdrop); }
  body { position: relative; font-family: "Questrial", "Century Gothic", sans-serif; color: var(--ink); }

  .page-label {
    position: absolute; top: 90px; font-family: "Open Sans", sans-serif;
    font-weight: 700; font-size: 12px; color: var(--label);
  }
  .page-label--left { left: 316px; }
  .page-label--right { left: 828px; }

  .spread { position: absolute; left: 81px; top: 122px; width: 1001px; height: 388px; display: flex; }

  .page-left { position: relative; width: 500px; height: 388px; background: var(--paper); }
  .hero-photo {
    position: absolute; left: 0; top: 0; width: 500px; height: 169px;
    background: linear-gradient(100deg, #b9c7d6 0%, #d9b9a0 30%, #f0d2bb 55%, #e9e4dc 80%, #d5d8dc 100%);
  }
  .feature-panel {
    position: absolute; left: 0; top: 176px; width: 500px; height: 212px;
    background: linear-gradient(180deg, var(--blue-top) 0%, var(--blue-bottom) 100%);
  }
  .accessory-photo {
    position: absolute; left: 20px; top: 18px; width: 160px; height: 172px;
    background: linear-gradient(160deg, rgba(40,60,90,.35) 0%, rgba(60,90,130,.25) 100%);
  }
  .feature-title {
    position: absolute; left: 202px; top: 42px; font-size: 26px; font-weight: 400;
    color: #fff; letter-spacing: .3px;
  }
  .feature-copy {
    position: absolute; left: 202px; top: 84px; width: 250px;
    font-size: 6.8px; line-height: 1.88; color: #e8f4fc;
  }
  .feature-copy p + p { margin-top: 6px; }

  .page-right { position: relative; width: 501px; height: 388px; background: var(--paper); }
  .unit-photo {
    position: absolute; left: 33px; top: 36px; width: 114px; height: 232px;
    background: linear-gradient(180deg, #eceef1 0%, var(--placeholder-grey) 100%);
  }
  .column { position: absolute; width: 124px; font-size: 6.2px; line-height: 1.4; }
  .column--one { left: 180px; top: 45px; }
  .column--two { left: 331px; top: 45px; width: 150px; }
  .column h2 {
    font-family: "Open Sans", sans-serif; font-weight: 700; font-size: 8.6px;
    line-height: 1.2; color: var(--green); margin-bottom: 5px;
  }
  .column p + p { margin-top: 6px; }
  .column section + section { margin-top: 18px; }
  .column--two section + section { margin-top: 28px; }
  .column strong { font-family: "Open Sans", sans-serif; font-weight: 700; }
</style>
</head>
<body>
  <div class="page-label page-label--left">Page 6</div>
  <div class="page-label page-label--right">Page 7</div>

  <main class="spread">
    <article class="page-left">
      <div class="hero-photo" role="img" aria-label="Photo of a smiling family of four sitting close together at home"></div>
      <section class="feature-panel">
        <div class="accessory-photo" role="img" aria-label="Photo of ducted vacuum accessories: hose, wand, floor heads and wall bracket"></div>
        <h1 class="feature-title">Ducted Vacuum</h1>
        <div class="feature-copy">
          <p>Ducted vacuums with Harrowgate Locks are the perfect accessory for keeping you home as good as new. With various units ranging from the smaller 2Hp - 2 to 4 outlet unit for the smaller home up to the 4Hp – 5 to 8 outlet unit for larger two story homes and everything in between.</p>
          <p>Don't get caught up wrestling with and dragging around a corded vacuum. Use a ducted system and all you'll need to carry is the wand.</p>
        </div>
      </section>
    </article>

    <article class="page-right">
      <div class="unit-photo" role="img" aria-label="Product photo of the ducted vacuum power unit"></div>

      <div class="column column--one">
        <section>
          <h2>A Southvale Vac ducted vacuum improves your health</h2>
          <p>Every day we breathe in billions of polluting particles around the home. In fact, <strong>the average house collects 18kg of dust a year!</strong> Along with other allergens this can have a major impact on health, especially for asthma and allergy sufferers.</p>
          <p>While portable vacuum cleaners appear to clean a room, they in fact release dust, bacteria and allergens back into the air. Southvale Vac ducted vacuum systems remove all vacuumed dust particles, allergens and noxious odours, creating a healthier living environment</p>
        </section>
        <section>
          <h2>Faster Easier Cleaning</h2>
          <p>Ducted vacuum systems are versatile enough to be used just about anywhere. Carpets, hard floors, curtains, skirtings, staircases, cars and verandas can all be cleaned with a ducted vacuum system – even the family pet (yes, we have actually tested this – results differ from pet to pet!).</p>
          <p>The longer hose and convenient inlet valves of a ducted vacuum help you to reach all parts of your house effortlessly. A Southvale Vac ducted vacuum will speed up and simplify how you clean your home, giving you more time for the important things in life – you and your family.</p>
        </section>
      </div>

      <div class="column column--two">
        <section>
          <h2>More Powerful Suction</h2>
          <p>A Southvale Vac ducted vacuum system <strong>has</strong> up to five times more power than most conventional portable vacuum cleaners.</p>
          <p>The heavy duty long-life motors used in all Southvale Vac systems ensure hard to shift dust and dirt will be removed from your valuable carpets, soft furnishings and other floor coverings, both protecting them and prolonging their lives. The ducted vacuum system also works well on curtains.</p>
        </section>
        <section>
          <h2>The Cost Effective Cleaning Solution</h2>
          <p>Did you know that most ducted vacuum systems cost roughly the same as a high quality portable vacuum cleaner? The differences are that ducted vacuum systems last considerably longer (up to four times in fact), are more robust and require less maintenance. It all adds up to a more cost effective investment. Southvale Vac ducted vacuum systems are a semi-permanent feature and an excellent selling point for your home. Why? They not only make cleaning a breeze, they are built to last. That combination will increase the value of your home – well in excess of the original purchase price! As a ducted vacuum system is a semi-permanent structure in your house, it is covered under building insurance.</p>
        </section>
      </div>
    </article>
  </main>
</body>
</html>
```